VOMRA Pty Ltd Business Card

Looking for a simple yet eye-catching double-sided business card design using my company logo on one side and contact details on the other.

Target Market(s)

Government

Industry/Entity Type

Communication Systems Engineering

Contact Information for Business Card

VOMRA Pty Ltd

Requirements
Nice to have
• Would be great to have a QR code so details can be scanned into contacts

```html
<!DOCTYPE html>
<html lang="en">
<head>
<meta charset="utf-8">
<title>VOMRA Pty Ltd Business Card</title>
<link href="https://fonts.googleapis.com/css2?family=Orbitron:wght@700;800&family=Poppins:wght@400&display=swap" rel="stylesheet">
<style>
  :root {
    --backdrop: #e3e3e3;
    --card: #ffffff;
    --ink: #2f3a40;
    --ink-soft: #3a4348;
  }
  * { margin: 0; padding: 0; box-sizing: border-box; }
  html, body { width: 1200px; height: 900px; overflow: hidden; }
  body { background: var(--backdrop); position: relative; font-family: "Poppins", sans-serif; color: var(--ink-soft); }

  .card {
    position: absolute;
    top: 217px;
    width: 309px;
    height: 499px;
    background: var(--card);
    box-shadow: 0 1px 3px rgba(0,0,0,0.12);
  }
  .card--front { left: 279px; border-radius: 0 42px 0 42px; }
  .card--back  { left: 617px; border-radius: 42px 0 42px 0; }

  .front-name {
    position: absolute;
    left: 0; right: 0;
    top: 224px;
    text-align: center;
    font-family: "Orbitron", sans-serif;
    font-weight: 800;
    font-size: 48px;
    letter-spacing: 2px;
    color: var(--ink);
  }

  .brand-name {
    position: absolute;
    left: 25px;
    top: 164px;
    font-family: "Orbitron", sans-serif;
    font-weight: 800;
    font-size: 42px;
    letter-spacing: 2px;
    color: var(--ink);
  }

  .person { position: absolute; left: 25px; top: 303px; }
  .person__name {
    font-family: "Orbitron", sans-serif;
    font-weight: 800;
    font-size: 20px;
    letter-spacing: 0.5px;
    color: var(--ink);
    text-transform: uppercase;
    line-height: 1.1;
  }
  .person__role { font-size: 14px; margin-top: 2px; }

  .contacts { position: absolute; left: 25px; top: 358px; list-style: none; }
  .contacts li { display: flex; align-items: center; gap: 5px; font-size: 14px; height: 18.5px; }
  .contacts svg { width: 12px; height: 12px; fill: var(--ink); flex: none; }

  .address { position: absolute; left: 27px; top: 427px; font-size: 14px; line-height: 18px; }
</style>
</head>
<body>
  <section class="card card--front">
    <div class="front-name">VOMRA</div>
  </section>

  <section class="card card--back">
    <div class="brand-name">VOMRA</div>

    <div class="person">
      <h1 class="person__name">Daniel Archer</h1>
      <p class="person__role">Managing Director</p>
    </div>

    <ul class="contacts">
      <li>
        <svg viewBox="0 0 24 24"><path d="M6.6 10.8a15.1 15.1 0 0 0 6.6 6.6l2.2-2.2a1 1 0 0 1 1-.25 11.4 11.4 0 0 0 3.6.57 1 1 0 0 1 1 1V20a1 1 0 0 1-1 1A17 17 0 0 1 3 4a1 1 0 0 1 1-1h3.5a1 1 0 0 1 1 1c0 1.25.2 2.45.57 3.57a1 1 0 0 1-.25 1z"/></svg>
        044-987 654 321
      </li>
      <li>
        <svg viewBox="0 0 24 24"><path d="M2 5h20v14H2z M2 5l10 8 10-8" fill="none" stroke="#2f3a40" stroke-width="0"/><path d="M2 6.5V19h20V6.5l-10 7.5z M2.5 5h19L12 12z"/></svg>
        hello@vomrasite.com
      </li>
      <li>
        <svg viewBox="0 0 24 24"><circle cx="12" cy="12" r="9.5" fill="none" stroke="#2f3a40" stroke-width="2"/><ellipse cx="12" cy="12" rx="4" ry="9.5" fill="none" stroke="#2f3a40" stroke-width="2"/><path d="M2.5 12h19" stroke="#2f3a40" stroke-width="2"/></svg>
        www.vomrasite.com
      </li>
    </ul>

    <p class="address">18, Harbour Street East<br>2150,Australia</p>
  </section>
</body>
</html>
```